Oakmere Animal Care Group of Central Pennsylvania

I need a business card design for a new company in Harrisburg PA called "Animal Care Oakmere Group of Central PA". I will be providing relief services for veterinarians who need coverage during vacations; sick/maternity leave, etc. I would like to see the veterinarian symbol incorporated in the design in combination with animals (dogs /cats/birds/reptiles an pocket pets). Include My full name: Tomás R. Quintaval DVM, MLAS, BS. Also include my e mail (dvmtrq@mailbrook.net) and phone number 5552846017

Target Market(s)

Small Animal Veterinarian, practice owner

Industry/Entity Type

Business

Contact Information for Business Card

Oakmere Animal Care Group of Central PA

Font styles to use
Script

Requirements
Must have
• Veterinarian caduceus (see image) and Small animals (pets) within the logo.
Nice to have
• Give a sense of relaxation (vacationing)
Should not have
• Large animals, i.e. horses, cows, zoo animals...

```html
<!DOCTYPE html>
<html lang="en">
<head>
<meta charset="utf-8">
<title>Animal Care Oakmere Group of Central PA – Business Card</title>
<link rel="stylesheet" href="https://fonts.googleapis.com/css2?family=Cinzel:wght@700&family=Kaushan+Script&family=Tinos&display=swap">
<style>
  :root {
    --page-bg: #e9e6e1;
    --card-bg: #ffffff;
    --ink: #1c1c1c;
    --accent-red: #c5262c;
    --divider: #b9b9b9;
  }
  html, body {
    margin: 0;
    width: 1200px;
    height: 892px;
    overflow: hidden;
    background: var(--page-bg);
  }
  .canvas {
    position: relative;
    width: 1200px;
    height: 892px;
  }
  .card {
    position: absolute;
    left: 100px;
    top: 160px;
    width: 1000px;
    height: 572px;
    background: var(--card-bg);
    box-shadow: 0 6px 24px rgba(0,0,0,0.18);
  }
  .card__divider {
    position: absolute;
    left: 0;
    top: 0;
  }
  .brand {
    position: absolute;
    left: 40px;
    top: 120px;
    width: 500px;
    text-align: center;
  }
  .brand__mark {
    display: block;
    margin: 0 auto 28px;
  }
  .brand__name {
    font-family: "Cinzel", serif;
    font-weight: 700;
    color: var(--ink);
    font-size: 30px;
    line-height: 1.25;
    letter-spacing: 0.5px;
    margin: 0;
  }
  .contact {
    position: absolute;
    left: 612px;
    top: 80px;
    width: 370px;
  }
  .contact__name {
    font-family: "Kaushan Script", cursive;
    color: var(--accent-red);
    font-size: 40px;
    line-height: 1.2;
    margin: 0 0 54px;
  }
  .contact__line {
    font-family: "Tinos", serif;
    color: var(--ink);
    margin: 0 0 14px;
  }
  .contact__phone { font-size: 36px; }
  .contact__email { font-size: 28px; }
</style>
</head>
<body>
<div class="canvas">
  <div class="card">
    <svg class="card__divider" width="1000" height="572" aria-hidden="true">
      <line x1="590" y1="0" x2="572" y2="572" stroke="var(--divider)" stroke-width="1.5"/>
    </svg>

    <div class="brand">
      <svg class="brand__mark" width="150" height="150" aria-hidden="true">
        <circle cx="75" cy="75" r="68" fill="none" stroke="var(--accent-red)" stroke-width="8"/>
      </svg>
      <p class="brand__name">Animal Care Oakmere Group<br>of Central PA</p>
    </div>

    <div class="contact">
      <p class="contact__name">Tomás R. Quintaval<br>DVM, MLAS, BS</p>
      <p class="contact__line contact__phone">5552846017</p>
      <p class="contact__line contact__email">dvmtrq@mailbrook.net</p>
    </div>
  </div>
</div>
</body>
</html>
```